Harrow Point Metrics Company Website Design and Coding

We want to redesign our existing website so that it is more visually and functionally appealing to prospective clients and potential job candidates. We would like to keep our current color scheme and implement our current logo as well. We have a high-level idea of website structure that we are thinking of, which is in the attached files. Logo is included as well. The final design would ideally be energy and analytics focused. We will need the new website to be coded as well, please.

Target Market(s)

Energy and utility industry

Industry/Entity Type

Energy/analytics

Coding

Coded - Design and coding required

Number of Pages Required

5+ page

Font styles to use
Sans Serif

Colors
0094D4
00A9DD
6FCCEA
C7EBF8
E9F6FB
F0912C
F2A743
F7CA91
FBE8D2
FDF5EE

Requirements
Must have
• Consistent color scheme- please use the one that we provided. We need an overview, a home page, and our core services. A separate job application page. Logo must be incorporated. We would like e "Meet our Team" page. Please include all of the content that is listed in our attachments.
Nice to have
• Movement
Should not have
• No music, no cartoons/animation, no pictures of a chalkboard

```html
<!DOCTYPE html>
<html lang="en">
<head>
<meta charset="utf-8">
<title>Harrow Point Metrics — Home Page Variants</title>
<link rel="stylesheet" href="https://fonts.googleapis.com/css2?family=Rajdhani:wght@500;600;700&family=Poppins:wght@400;500;600&display=swap">
<style>
:root{
  --blue:#0094D4;
  --blue-2:#00A9DD;
  --blue-3:#6FCCEA;
  --blue-4:#C7EBF8;
  --blue-5:#E9F6FB;
  --stage:#7a7a7a;
  --ink:#3a3a3a;
  --muted:#6f6f6f;
  --light:#f1f1f1;
  --card-gray:#8f8f8f;
  --footer:#1e1f21;
  --head:"Rajdhani",sans-serif;
  --body:"Poppins",sans-serif;
}
*{margin:0;padding:0;box-sizing:border-box}
html,body{width:1200px;height:777px;overflow:hidden;background:var(--stage)}
.stage{position:relative;width:1200px;height:777px}
.page{position:absolute;top:40px;width:195px;height:696px;background:#fff;overflow:hidden;font-family:var(--body);color:var(--ink)}
.page section,.page header,.page footer{position:absolute;left:0;width:195px}

/* header */
.site-header{top:0;height:20px;background:#fff}
.topbar{position:absolute;right:0;top:0;width:98px;height:6px;background:var(--blue);display:flex;align-items:center;gap:3px;padding-left:6px;font-size:1.7px;color:#fff;white-space:nowrap}
.topbar .dot{width:3.4px;height:3.4px;border-radius:50%;background:#fff;opacity:.85}
.brand{position:absolute;left:18px;top:8px;display:flex;align-items:center;gap:2px;font-size:3.6px;color:#777;font-family:var(--head);font-weight:500;white-space:nowrap}
.brand .mark{width:5px;height:5px;border-radius:50%;background:var(--blue-4)}
.nav{position:absolute;left:82px;top:12px;display:flex;gap:5px;font-size:2px;color:#555;white-space:nowrap}
.nav .active{color:var(--blue)}

/* hero */
.hero{top:20px;height:116px}
.hero .slide{position:absolute;inset:0}
.hero-1 .slide{background:linear-gradient(135deg,#0c1a5e 0%,#2540c9 45%,#7a3bd0 75%,#18207a 100%)}
.hero-2 .slide{background:linear-gradient(180deg,#7fb6e4 0%,#cfe3f0 40%,#6a9e3a 60%,#2f5e1d 100%)}
.hero-3 .slide{background:linear-gradient(180deg,#b9d3ea 0%,#8fb0cf 40%,#2e5ea6 65%,#1c3b78 100%)}
.hero-4 .slide{background:radial-gradient(circle at 50% 45%,#e9f6d0 0%,#8fc640 35%,#3c7a22 70%,#1f4a14 100%)}
.hero-5 .slide{background:linear-gradient(180deg,#5aa4dc 0%,#a9d0ee 35%,#eef4fa 60%,#d9e6f2 100%)}
.hero-title{position:absolute;left:18px;top:44px;background:var(--blue);color:#fff;font-family:var(--head);font-weight:600;font-size:7.2px;padding:1px 4px;white-space:nowrap}
.hero-sub{position:absolute;left:18px;top:55px;width:118px;background:rgba(40,40,40,.45);color:#fff;font-family:var(--head);font-weight:500;font-size:5px;line-height:7px;padding:1px 4px}
.hero-dots{position:absolute;left:91px;top:103px;display:flex;gap:2px}
.hero-dots i{width:2px;height:2px;border-radius:50%;background:#fff;opacity:.7}
.hero-dots i.on{background:var(--blue-3);opacity:1}
.hero-curve{position:absolute;left:0;bottom:0;width:195px;height:20px}

/* welcome */
.welcome{top:136px;height:85px}
.welcome .kicker{position:absolute;left:18px;top:11px;font-family:var(--head);font-size:4.8px;font-weight:500}
.welcome h2{position:absolute;left:18px;top:17px;font-family:var(--head);font-weight:600;font-size:6.2px;color:var(--blue)}
.welcome p{position:absolute;left:18px;top:29px;width:82px;font-size:1.95px;line-height:3.3px;color:var(--muted);text-align:justify}
.btn{display:inline-block;background:var(--blue);color:#fff;font-size:1.9px;font-weight:600;padding:1.6px 4px;text-transform:uppercase}
.welcome .btn{position:absolute;left:18px;top:64px}
.welcome .deco{position:absolute;left:112px;top:12px;width:46px;height:64px;border-radius:40% 60% 30% 70%;background:radial-gradient(circle at 40% 35%,var(--blue-3),var(--blue-4) 55%,rgba(199,235,248,0) 75%)}

/* services */
.services{top:221px;height:103px;background:var(--light)}
.section-title{position:absolute;left:0;width:195px;text-align:center;font-family:var(--head);font-weight:500;font-size:6.4px}
.section-title b{font-weight:600;color:var(--blue)}
.section-title::after{content:"";display:block;width:8px;height:.6px;background:var(--blue);margin:1.2px auto 0}
.services .section-title{top:5px}
.svc-row{position:absolute;left:18px;top:20px;display:flex;gap:3.5px}
.svc{width:37px;height:72px;border-radius:2px;overflow:hidden;display:flex;flex-direction:column;color:#fff}
.svc .photo{height:34px;background:linear-gradient(180deg,#4b8fd6 0%,#a6cbe6 45%,#e3c25b 75%,#4f8a2a 100%)}
.svc:nth-child(2) .photo{background:linear-gradient(160deg,#9bc4e6,#6aa440 45%,#2b5d1a)}
.svc:nth-child(3) .photo{background:linear-gradient(180deg,#6fb0e6,#cfe3f0 55%,#7fb13a)}
.svc:nth-child(4) .photo{background:linear-gradient(180deg,#2f6fb8,#f2a743 45%,#5d9a2a)}
.svc .body{flex:1;padding:3px 2px 2.5px;text-align:center;display:flex;flex-direction:column;align-items:center}
.svc.blue .body{background:var(--blue)}
.svc.gray .body{background:var(--card-gray)}
.svc h3{font-size:2.05px;font-weight:600;line-height:3px;min-height:6px;display:flex;align-items:center}
.svc p{font-size:1.65px;line-height:2.7px;margin-top:1.6px}
.svc .more{margin-top:auto;border:.3px solid #fff;font-size:1.6px;padding:.8px 3px}
.arrow{position:absolute;top:53px;width:5.5px;height:5.5px;border-radius:50%;border:.4px solid #999;background:#fff}
.arrow svg{width:100%;height:100%;display:block}
.arrow.left{left:9px}
.arrow.right{left:181px}
.services .fade{position:absolute;top:2px;left:2px;width:22px;height:30px;border-radius:50%;background:radial-gradient(circle,var(--blue-4),rgba(199,235,248,0) 70%)}
.services .fade.r{left:172px;top:66px}

/* publications */
.publications{top:324px;height:134px}
.publications .section-title{top:6px}
.pub-img{position:absolute;width:79px;height:49px}
.pub-img.a{left:18px;top:22px;background:radial-gradient(circle at 60% 60%,#f2a743 0%,#3a6fae 35%,#0f2a55 80%)}
.pub-img.b{left:97px;top:71px;background:linear-gradient(135deg,#0c2240 0%,#1d5b8f 45%,#6fccea 70%,#112a48 100%)}
.pub-text{position:absolute;width:68px}
.pub-text.a{left:105px;top:30px}
.pub-text.b{left:23px;top:80px}
.pub-text h3{font-family:var(--head);font-weight:600;font-size:4px;color:var(--blue)}
.pub-text p{font-size:1.75px;line-height:3px;color:var(--muted);margin-top:1.6px}
.btn-outline{display:inline-block;margin-top:3px;border:.4px solid var(--blue);color:var(--blue);font-size:1.7px;padding:1.2px 3px;text-transform:uppercase}

/* team */
.team{top:458px;height:92px}
.team .section-title{top:9px}
.team-row{position:absolute;left:18px;top:26px;display:flex;gap:8.7px}
.member{position:relative;width:33px;height:51px;background:#fff;box-shadow:0 .5px 2px rgba(0,0,0,.18);text-align:center;padding-top:14px}
.member .avatar{position:absolute;left:8.5px;top:-2px;width:16px;height:16px;border-radius:50%;background:linear-gradient(180deg,#c9ccd1,#6b7280)}
.member h3{font-size:1.9px;font-weight:600;color:var(--blue);white-space:nowrap}
.member .role{font-size:1.5px;color:var(--muted);margin-top:.3px}
.member p{font-size:1.45px;line-height:2.5px;color:var(--muted);padding:1.5px 2px 0}
.member .go{position:absolute;left:14px;bottom:-2.5px;width:5px;height:5px;border-radius:50%;background:var(--blue)}
.member .go svg{width:100%;height:100%;display:block}

/* about */
.about{top:550px;height:86px;background:linear-gradient(90deg,#8a7a5a 0%,#d8c69c 25%,#f3eee2 55%,#f4f4f4 100%)}
.about .text{position:absolute;left:113px;top:9px;width:58px}
.about h2{font-family:var(--head);font-weight:500;font-size:6.6px;color:var(--blue)}
.about p{font-size:1.62px;line-height:2.9px;color:var(--muted);text-align:justify;margin-top:1.5px}
.about .btn{background:#9a9a9a;margin-top:3px}
.about-curve{position:absolute;left:0;bottom:0;width:195px;height:16px}

/* footer */
.site-footer{top:636px;height:60px;background:var(--footer);color:#cfcfcf}
.site-footer .brand{left:0;width:195px;justify-content:center;top:4px;font-size:4.8px;color:#bdbdbd}
.site-footer .brand .mark{background:#555;width:5px;height:5px}
.footer-nav{position:absolute;left:0;width:195px;top:17px;display:flex;justify-content:center;gap:5px;font-size:1.7px;font-weight:600;text-transform:uppercase;color:#e5e5e5}
.contact{position:absolute;top:27px;display:flex;align-items:center;gap:3px;font-size:1.6px;line-height:2.5px}
.contact.addr{left:25px}
.contact.phone{left:89px}
.contact .ico{width:6px;height:6px;border-radius:50%;border:.4px solid #ccc;flex:none}
.contact .ico svg{width:100%;height:100%;display:block}
.getin{position:absolute;left:135px;top:28px;border:.4px solid var(--blue);color:var(--blue);font-size:1.6px;padding:1.3px 4px}
.socials{position:absolute;left:18px;top:50px;display:flex;gap:1.5px}
.socials i{width:6px;height:6px;border-radius:50%;border:.4px solid #ccc}
.copy{position:absolute;left:122px;top:52px;font-size:1.6px;color:#bbb;white-space:nowrap}
</style>
</head>
<body>
<main class="stage">

<!-- variant 1 -->
<article class="page" style="left:44px">
  <header class="site-header">
    <div class="topbar"><span>555.210.4478</span><span>hello@harrowpointmetrics.test</span><i class="dot"></i><i class="dot"></i><i class="dot"></i></div>
    <div class="brand"><span class="mark"></span>Harrow Point Metrics</div>
    <nav class="nav"><span class="active">Home</span><span>Core Services</span><span>About Us</span><span>Our Work</span><span>Blog</span><span>Contact Us</span></nav>
  </header>
  <section class="hero hero-1">
    <div class="slide" role="img" aria-label="Photo of a hand over glowing financial data screens"></div>
    <div class="hero-title">Harrow Point Metrics</div>
    <div class="hero-sub">Data driven research and insights<br>to build a smarter and cleaner energy future</div>
    <div class="hero-dots"><i class="on"></i><i></i><i></i></div>
    <svg class="hero-curve" viewBox="0 0 195 20" preserveAspectRatio="none"><path d="M0 6 Q97 26 195 0 L195 20 L0 20Z" fill="#fff"/><path d="M0 6 Q97 26 195 0" fill="none" stroke="#0094D4" stroke-width="1.2"/></svg>
  </section>
  <section class="welcome">
    <div class="kicker">Welcome To</div>
    <h2>Harrow Point Metrics</h2>
    <p>Harrow Point Metrics was formed in 2016 to help utilities and regulatory agencies navigate the technical, economic, and policy challenges of building a smarter and cleaner energy future. Through careful research design and sound analysis methods we give program administrators clear, data-driven insights into how technologies and interventions affect the way homes and businesses use energy.</p>
    <span class="btn">Read More</span>
    <div class="deco" role="img" aria-label="Dotted blue wave graphic"></div>
  </section>
  <section class="services">
    <div class="fade"></div><div class="fade r"></div>
    <h2 class="section-title">Our <b>Services</b></h2>
    <span class="arrow left"><svg viewBox="0 0 10 10"><path d="M6 3 L4 5 L6 7" fill="none" stroke="#888" stroke-width=".8"/></svg></span>
    <div class="svc-row">
      <div class="svc blue"><div class="photo" role="img" aria-label="Wind turbines over solar panels"></div><div class="body"><h3>Predictive Analytics and Forecasting</h3><p>Distributed energy resource integration into planning and operations</p><span class="more">Read More</span></div></div>
      <div class="svc gray"><div class="photo" role="img" aria-label="Rows of solar panels in a field"></div><div class="body"><h3>T&amp;D Planning</h3><p>Location specific, probabilistic forecasting for transmission and distribution planning</p><span class="more">Read More</span></div></div>
      <div class="svc blue"><div class="photo" role="img" aria-label="Wind turbines on green hills"></div><div class="body"><h3>Pilot &amp; Emerging Tech Support</h3><p>Design and implementation of pilots and controlled deployments</p><span class="more">Read More</span></div></div>
      <div class="svc gray"><div class="photo" role="img" aria-label="Turbines at sunset"></div><div class="body"><h3>Program Portfolio &amp; Resource Planning</h3><p>End-use load profile studies, saturation research and baseline studies</p><span class="more">Read More</span></div></div>
    </div>
    <span class="arrow right"><svg viewBox="0 0 10 10"><path d="M4 3 L6 5 L4 7" fill="none" stroke="#888" stroke-width=".8"/></svg></span>
  </section>
  <section class="publications">
    <h2 class="section-title">Publications</h2>
    <div class="pub-img a" role="img" aria-label="City lights seen from above at night"></div>
    <div class="pub-text a"><h3>Conference Presentations</h3><p>We share our methods and findings at industry events, covering load impact evaluation, grid planning studies, forecasting models and lessons learned from pilot programs across the country.</p><span class="btn-outline">Read More</span></div>
    <div class="pub-text b"><h3>Reports</h3><p>Our published reports document program impacts, end-use load research, emerging technology pilots and forecasting work prepared for utilities, regulators and research partners.</p><span class="btn-outline">Read More</span></div>
    <div class="pub-img b" role="img" aria-label="Hand pointing at data charts on a screen"></div>
  </section>
  <section class="team">
    <h2 class="section-title">Our <b>Team</b></h2>
    <div class="team-row">
      <div class="member"><div class="avatar" role="img" aria-label="Portrait of Owen Marlow"></div><h3>Owen Marlow, M.S.</h3><div class="role">Partner</div><p>Owen is an applied statistician whose work is centered on estimating the impacts of demand programs.</p><span class="go"><svg viewBox="0 0 10 10"><path d="M3 5 H7 M5.5 3.5 L7 5 L5.5 6.5" fill="none" stroke="#fff" stroke-width=".8"/></svg></span></div>
      <div class="member"><div class="avatar" role="img" aria-label="Portrait of Theo Varga"></div><h3>Theo Varga, M.P.P.</h3><div class="role">Partner</div><p>Theo specializes in advanced analytics using large volumes of hourly and sub-hourly data.</p><span class="go"><svg viewBox="0 0 10 10"><path d="M3 5 H7 M5.5 3.5 L7 5 L5.5 6.5" fill="none" stroke="#fff" stroke-width=".8"/></svg></span></div>
      <div class="member"><div class="avatar" role="img" aria-label="Portrait of Mira Coltrane"></div><h3>Mira Coltrane</h3><div class="role">Partner</div><p>Mira's work has focused on distributed energy resources, from solar panels to electric vehicles.</p><span class="go"><svg viewBox="0 0 10 10"><path d="M3 5 H7 M5.5 3.5 L7 5 L5.5 6.5" fill="none" stroke="#fff" stroke-width=".8"/></svg></span></div>
      <div class="member"><div class="avatar" role="img" aria-label="Portrait of Lena Hartwell"></div><h3>Lena Hartwell, M.S.</h3><div class="role">Partner</div><p>Lena has extensive expertise with analysis of smart meter data and rate design.</p><span class="go"><svg viewBox="0 0 10 10"><path d="M3 5 H7 M5.5 3.5 L7 5 L5.5 6.5" fill="none" stroke="#fff" stroke-width=".8"/></svg></span></div>
    </div>
  </section>
  <section class="about" role="img" aria-label="Wind turbine on a hillside at sunrise">
    <div class="text"><h2>About Us</h2><p>Harrow Point Metrics was formed in 2016 to help utilities and regulatory agencies navigate the technical, economic, and policy challenges of building a smarter and cleaner energy future. Our research focuses on impact analysis as well as predictive and causal analytics. We deliver data-driven insights into how technologies and interventions affect the way homes and businesses use energy and how those in turn affect grid and system planning.</p><span class="btn">Read More</span></div>
    <svg class="about-curve" viewBox="0 0 195 16" preserveAspectRatio="none"><path d="M0 12 Q110 -2 195 10 L195 16 L0 16Z" fill="#1e1f21"/><path d="M0 12 Q110 -2 195 10" fill="none" stroke="#0094D4" stroke-width="1.2"/></svg>
  </section>
  <footer class="site-footer">
    <div class="brand"><span class="mark"></span>Harrow Point Metrics</div>
    <nav class="footer-nav"><span>Home</span><span>Core Services</span><span>About Us</span><span>Our Work</span><span>Blog</span><span>Contact Us</span></nav>
    <div class="contact addr"><span class="ico"><svg viewBox="0 0 10 10"><path d="M5 2.5 a1.8 1.8 0 0 1 1.8 1.8 C6.8 5.6 5 7.5 5 7.5 S3.2 5.6 3.2 4.3 A1.8 1.8 0 0 1 5 2.5Z" fill="#ccc"/></svg></span><span>48 Larkfield Row<br>Suite 2 Brenton, OR 97000</span></div>
    <div class="contact phone"><span class="ico"><svg viewBox="0 0 10 10"><path d="M3.4 2.8 L4.4 2.8 L4.9 4.2 L4.2 4.7 Q4.8 5.8 5.6 6.2 L6.1 5.5 L7.2 6 L7.2 7 Q4.5 7.2 3.4 2.8Z" fill="#ccc"/></svg></span><span>555.210.4478</span></div>
    <span class="getin">Get In Touch</span>
    <div class="socials"><i></i><i></i><i></i></div>
    <div class="copy">© 2022 Harrow Point Metrics All rights reserved</div>
  </footer>
</article>

<!-- variant 2 -->
<article class="page" style="left:271px">
  <header class="site-header">
    <div class="topbar"><span>555.210.4478</span><span>hello@harrowpointmetrics.test</span><i class="dot"></i><i class="dot"></i><i class="dot"></i></div>
    <div class="brand"><span class="mark"></span>Harrow Point Metrics</div>
    <nav class="nav"><span class="active">Home</span><span>Core Services</span><span>About Us</span><span>Our Work</span><span>Blog</span><span>Contact Us</span></nav>
  </header>
  <section class="hero hero-2">
    <div class="slide" role="img" aria-label="Photo of wind turbines in a green field under blue sky"></div>
    <div class="hero-title">Harrow Point Metrics</div>
    <div class="hero-sub">Data driven research and insights<br>to build a smarter and cleaner energy future</div>
    <div class="hero-dots"><i></i><i class="on"></i><i></i></div>
    <svg class="hero-curve" viewBox="0 0 195 20" preserveAspectRatio="none"><path d="M0 6 Q97 26 195 0 L195 20 L0 20Z" fill="#fff"/><path d="M0 6 Q97 26 195 0" fill="none" stroke="#0094D4" stroke-width="1.2"/></svg>
  </section>
  <section class="welcome">
    <div class="kicker">Welcome To</div>
    <h2>Harrow Point Metrics</h2>
    <p>Harrow Point Metrics was formed in 2016 to help utilities and regulatory agencies navigate the technical, economic, and policy challenges of building a smarter and cleaner energy future. Through careful research design and sound analysis methods we give program administrators clear, data-driven insights into how technologies and interventions affect the way homes and businesses use energy.</p>
    <span class="btn">Read More</span>
    <div class="deco" role="img" aria-label="Dotted blue wave graphic"></div>
  </section>
  <section class="services">
    <div class="fade"></div><div class="fade r"></div>
    <h2 class="section-title">Our <b>Services</b></h2>
    <span class="arrow left"><svg viewBox="0 0 10 10"><path d="M6 3 L4 5 L6 7" fill="none" stroke="#888" stroke-width=".8"/></svg></span>
    <div class="svc-row">
      <div class="svc blue"><div class="photo" role="img" aria-label="Wind turbines over solar panels"></div><div class="body"><h3>Predictive Analytics and Forecasting</h3><p>Distributed energy resource integration into planning and operations</p><span class="more">Read More</span></div></div>
      <div class="svc gray"><div class="photo" role="img" aria-label="Rows of solar panels in a field"></div><div class="body"><h3>T&amp;D Planning</h3><p>Location specific, probabilistic forecasting for transmission and distribution planning</p><span class="more">Read More</span></div></div>
      <div class="svc blue"><div class="photo" role="img" aria-label="Wind turbines on green hills"></div><div class="body"><h3>Pilot &amp; Emerging Tech Support</h3><p>Design and implementation of pilots and controlled deployments</p><span class="more">Read More</span></div></div>
      <div class="svc gray"><div class="photo" role="img" aria-label="Turbines at sunset"></div><div class="body"><h3>Program Portfolio &amp; Resource Planning</h3><p>End-use load profile studies, saturation research and baseline studies</p><span class="more">Read More</span></div></div>
    </div>
    <span class="arrow right"><svg viewBox="0 0 10 10"><path d="M4 3 L6 5 L4 7" fill="none" stroke="#888" stroke-width=".8"/></svg></span>
  </section>
  <section class="publications">
    <h2 class="section-title">Publications</h2>
    <div class="pub-img a" role="img" aria-label="City lights seen from above at night"></div>
    <div class="pub-text a"><h3>Conference Presentations</h3><p>We share our methods and findings at industry events, covering load impact evaluation, grid planning studies, forecasting models and lessons learned from pilot programs across the country.</p><span class="btn-outline">Read More</span></div>
    <div class="pub-text b"><h3>Reports</h3><p>Our published reports document program impacts, end-use load research, emerging technology pilots and forecasting work prepared for utilities, regulators and research partners.</p><span class="btn-outline">Read More</span></div>
    <div class="pub-img b" role="img" aria-label="Hand pointing at data charts on a screen"></div>
  </section>
  <section class="team">
    <h2 class="section-title">Our <b>Team</b></h2>
    <div class="team-row">
      <div class="member"><div class="avatar" role="img" aria-label="Portrait of Owen Marlow"></div><h3>Owen Marlow, M.S.</h3><div class="role">Partner</div><p>Owen is an applied statistician whose work is centered on estimating the impacts of demand programs.</p><span class="go"><svg viewBox="0 0 10 10"><path d="M3 5 H7 M5.5 3.5 L7 5 L5.5 6.5" fill="none" stroke="#fff" stroke-width=".8"/></svg></span></div>
      <div class="member"><div class="avatar" role="img" aria-label="Portrait of Theo Varga"></div><h3>Theo Varga, M.P.P.</h3><div class="role">Partner</div><p>Theo specializes in advanced analytics using large volumes of hourly and sub-hourly data.</p><span class="go"><svg viewBox="0 0 10 10"><path d="M3 5 H7 M5.5 3.5 L7 5 L5.5 6.5" fill="none" stroke="#fff" stroke-width=".8"/></svg></span></div>
      <div class="member"><div class="avatar" role="img" aria-label="Portrait of Mira Coltrane"></div><h3>Mira Coltrane</h3><div class="role">Partner</div><p>Mira's work has focused on distributed energy resources, from solar panels to electric vehicles.</p><span class="go"><svg viewBox="0 0 10 10"><path d="M3 5 H7 M5.5 3.5 L7 5 L5.5 6.5" fill="none" stroke="#fff" stroke-width=".8"/></svg></span></div>
      <div class="member"><div class="avatar" role="img" aria-label="Portrait of Lena Hartwell"></div><h3>Lena Hartwell, M.S.</h3><div class="role">Partner</div><p>Lena has extensive expertise with analysis of smart meter data and rate design.</p><span class="go"><svg viewBox="0 0 10 10"><path d="M3 5 H7 M5.5 3.5 L7 5 L5.5 6.5" fill="none" stroke="#fff" stroke-width=".8"/></svg></span></div>
    </div>
  </section>
  <section class="about" role="img" aria-label="Wind turbine on a hillside at sunrise">
    <div class="text"><h2>About Us</h2><p>Harrow Point Metrics was formed in 2016 to help utilities and regulatory agencies navigate the technical, economic, and policy challenges of building a smarter and cleaner energy future. Our research focuses on impact analysis as well as predictive and causal analytics. We deliver data-driven insights into how technologies and interventions affect the way homes and businesses use energy and how those in turn affect grid and system planning.</p><span class="btn">Read More</span></div>
    <svg class="about-curve" viewBox="0 0 195 16" preserveAspectRatio="none"><path d="M0 12 Q110 -2 195 10 L195 16 L0 16Z" fill="#1e1f21"/><path d="M0 12 Q110 -2 195 10" fill="none" stroke="#0094D4" stroke-width="1.2"/></svg>
  </section>
  <footer class="site-footer">
    <div class="brand"><span class="mark"></span>Harrow Point Metrics</div>
    <nav class="footer-nav"><span>Home</span><span>Core Services</span><span>About Us</span><span>Our Work</span><span>Blog</span><span>Contact Us</span></nav>
    <div class="contact addr"><span class="ico"><svg viewBox="0 0 10 10"><path d="M5 2.5 a1.8 1.8 0 0 1 1.8 1.8 C6.8 5.6 5 7.5 5 7.5 S3.2 5.6 3.2 4.3 A1.8 1.8 0 0 1 5 2.5Z" fill="#ccc"/></svg></span><span>48 Larkfield Row<br>Suite 2 Brenton, OR 97000</span></div>
    <div class="contact phone"><span class="ico"><svg viewBox="0 0 10 10"><path d="M3.4 2.8 L4.4 2.8 L4.9 4.2 L4.2 4.7 Q4.8 5.8 5.6 6.2 L6.1 5.5 L7.2 6 L7.2 7 Q4.5 7.2 3.4 2.8Z" fill="#ccc"/></svg></span><span>555.210.4478</span></div>
    <span class="getin">Get In Touch</span>
    <div class="socials"><i></i><i></i><i></i></div>
    <div class="copy">© 2022 Harrow Point Metrics All rights reserved</div>
  </footer>
</article>

<!-- variant 3 -->
<article class="page" style="left:498px">
  <header class="site-header">
    <div class="topbar"><span>555.210.4478</span><span>hello@harrowpointmetrics.test</span><i class="dot"></i><i class="dot"></i><i class="dot"></i></div>
    <div class="brand"><span class="mark"></span>Harrow Point Metrics</div>
    <nav class="nav"><span class="active">Home</span><span>Core Services</span><span>About Us</span><span>Our Work</span><span>Blog</span><span>Contact Us</span></nav>
  </header>
  <section class="hero hero-3">
    <div class="slide" role="img" aria-label="Photo of wind turbines and solar panels before blue mountains"></div>
    <div class="hero-title">Harrow Point Metrics</div>
    <div class="hero-sub">Data driven research and insights<br>to build a smarter and cleaner energy future</div>
    <div class="hero-dots"><i></i><i></i><i class="on"></i></div>
    <svg class="hero-curve" viewBox="0 0 195 20" preserveAspectRatio="none"><path d="M0 6 Q97 26 195 0 L195 20 L0 20Z" fill="#fff"/><path d="M0 6 Q97 26 195 0" fill="none" stroke="#0094D4" stroke-width="1.2"/></svg>
  </section>
  <section class="welcome">
    <div class="kicker">Welcome To</div>
    <h2>Harrow Point Metrics</h2>
    <p>Harrow Point Metrics was formed in 2016 to help utilities and regulatory agencies navigate the technical, economic, and policy challenges of building a smarter and cleaner energy future. Through careful research design and sound analysis methods we give program administrators clear, data-driven insights into how technologies and interventions affect the way homes and businesses use energy.</p>
    <span class="btn">Read More</span>
    <div class="deco" role="img" aria-label="Dotted blue wave graphic"></div>
  </section>
  <section class="services">
    <div class="fade"></div><div class="fade r"></div>
    <h2 class="section-title">Our <b>Services</b></h2>
    <span class="arrow left"><svg viewBox="0 0 10 10"><path d="M6 3 L4 5 L6 7" fill="none" stroke="#888" stroke-width=".8"/></svg></span>
    <div class="svc-row">
      <div class="svc blue"><div class="photo" role="img" aria-label="Wind turbines over solar panels"></div><div class="body"><h3>Predictive Analytics and Forecasting</h3><p>Distributed energy resource integration into planning and operations</p><span class="more">Read More</span></div></div>
      <div class="svc gray"><div class="photo" role="img" aria-label="Rows of solar panels in a field"></div><div class="body"><h3>T&amp;D Planning</h3><p>Location specific, probabilistic forecasting for transmission and distribution planning</p><span class="more">Read More</span></div></div>
      <div class="svc blue"><div class="photo" role="img" aria-label="Wind turbines on green hills"></div><div class="body"><h3>Pilot &amp; Emerging Tech Support</h3><p>Design and implementation of pilots and controlled deployments</p><span class="more">Read More</span></div></div>
      <div class="svc gray"><div class="photo" role="img" aria-label="Turbines at sunset"></div><div class="body"><h3>Program Portfolio &amp; Resource Planning</h3><p>End-use load profile studies, saturation research and baseline studies</p><span class="more">Read More</span></div></div>
    </div>
    <span class="arrow right"><svg viewBox="0 0 10 10"><path d="M4 3 L6 5 L4 7" fill="none" stroke="#888" stroke-width=".8"/></svg></span>
  </section>
  <section class="publications">
    <h2 class="section-title">Publications</h2>
    <div class="pub-img a" role="img" aria-label="City lights seen from above at night"></div>
    <div class="pub-text a"><h3>Conference Presentations</h3><p>We share our methods and findings at industry events, covering load impact evaluation, grid planning studies, forecasting models and lessons learned from pilot programs across the country.</p><span class="btn-outline">Read More</span></div>
    <div class="pub-text b"><h3>Reports</h3><p>Our published reports document program impacts, end-use load research, emerging technology pilots and forecasting work prepared for utilities, regulators and research partners.</p><span class="btn-outline">Read More</span></div>
    <div class="pub-img b" role="img" aria-label="Hand pointing at data charts on a screen"></div>
  </section>
  <section class="team">
    <h2 class="section-title">Our <b>Team</b></h2>
    <div class="team-row">
      <div class="member"><div class="avatar" role="img" aria-label="Portrait of Owen Marlow"></div><h3>Owen Marlow, M.S.</h3><div class="role">Partner</div><p>Owen is an applied statistician whose work is centered on estimating the impacts of demand programs.</p><span class="go"><svg viewBox="0 0 10 10"><path d="M3 5 H7 M5.5 3.5 L7 5 L5.5 6.5" fill="none" stroke="#fff" stroke-width=".8"/></svg></span></div>
      <div class="member"><div class="avatar" role="img" aria-label="Portrait of Theo Varga"></div><h3>Theo Varga, M.P.P.</h3><div class="role">Partner</div><p>Theo specializes in advanced analytics using large volumes of hourly and sub-hourly data.</p><span class="go"><svg viewBox="0 0 10 10"><path d="M3 5 H7 M5.5 3.5 L7 5 L5.5 6.5" fill="none" stroke="#fff" stroke-width=".8"/></svg></span></div>
      <div class="member"><div class="avatar" role="img" aria-label="Portrait of Mira Coltrane"></div><h3>Mira Coltrane</h3><div class="role">Partner</div><p>Mira's work has focused on distributed energy resources, from solar panels to electric vehicles.</p><span class="go"><svg viewBox="0 0 10 10"><path d="M3 5 H7 M5.5 3.5 L7 5 L5.5 6.5" fill="none" stroke="#fff" stroke-width=".8"/></svg></span></div>
      <div class="member"><div class="avatar" role="img" aria-label="Portrait of Lena Hartwell"></div><h3>Lena Hartwell, M.S.</h3><div class="role">Partner</div><p>Lena has extensive expertise with analysis of smart meter data and rate design.</p><span class="go"><svg viewBox="0 0 10 10"><path d="M3 5 H7 M5.5 3.5 L7 5 L5.5 6.5" fill="none" stroke="#fff" stroke-width=".8"/></svg></span></div>
    </div>
  </section>
  <section class="about" role="img" aria-label="Wind turbine on a hillside at sunrise">
    <div class="text"><h2>About Us</h2><p>Harrow Point Metrics was formed in 2016 to help utilities and regulatory agencies navigate the technical, economic, and policy challenges of building a smarter and cleaner energy future. Our research focuses on impact analysis as well as predictive and causal analytics. We deliver data-driven insights into how technologies and interventions affect the way homes and businesses use energy and how those in turn affect grid and system planning.</p><span class="btn">Read More</span></div>
    <svg class="about-curve" viewBox="0 0 195 16" preserveAspectRatio="none"><path d="M0 12 Q110 -2 195 10 L195 16 L0 16Z" fill="#1e1f21"/><path d="M0 12 Q110 -2 195 10" fill="none" stroke="#0094D4" stroke-width="1.2"/></svg>
  </section>
  <footer class="site-footer">
    <div class="brand"><span class="mark"></span>Harrow Point Metrics</div>
    <nav class="footer-nav"><span>Home</span><span>Core Services</span><span>About Us</span><span>Our Work</span><span>Blog</span><span>Contact Us</span></nav>
    <div class="contact addr"><span class="ico"><svg viewBox="0 0 10 10"><path d="M5 2.5 a1.8 1.8 0 0 1 1.8 1.8 C6.8 5.6 5 7.5 5 7.5 S3.2 5.6 3.2 4.3 A1.8 1.8 0 0 1 5 2.5Z" fill="#ccc"/></svg></span><span>48 Larkfield Row<br>Suite 2 Brenton, OR 97000</span></div>
    <div class="contact phone"><span class="ico"><svg viewBox="0 0 10 10"><path d="M3.4 2.8 L4.4 2.8 L4.9 4.2 L4.2 4.7 Q4.8 5.8 5.6 6.2 L6.1 5.5 L7.2 6 L7.2 7 Q4.5 7.2 3.4 2.8Z" fill="#ccc"/></svg></span><span>555.210.4478</span></div>
    <span class="getin">Get In Touch</span>
    <div class="socials"><i></i><i></i><i></i></div>
    <div class="copy">© 2022 Harrow Point Metrics All rights reserved</div>
  </footer>
</article>

<!-- variant 4 -->
<article class="page" style="left:727px">
  <header class="site-header">
    <div class="topbar"><span>555.210.4478</span><span>hello@harrowpointmetrics.test</span><i class="dot"></i><i class="dot"></i><i class="dot"></i></div>
    <div class="brand"><span class="mark"></span>Harrow Point Metrics</div>
    <nav class="nav"><span class="active">Home</span><span>Core Services</span><span>About Us</span><span>Our Work</span><span>Blog</span><span>Contact Us</span></nav>
  </header>
  <section class="hero hero-4">
    <div class="slide" role="img" aria-label="Photo looking up into a green forest canopy"></div>
    <div class="hero-title">Harrow Point Metrics</div>
    <div class="hero-sub">Data driven research and insights<br>to build a smarter and cleaner energy future</div>
    <div class="hero-dots"><i></i><i class="on"></i><i></i></div>
    <svg class="hero-curve" viewBox="0 0 195 20" preserveAspectRatio="none"><path d="M0 6 Q97 26 195 0 L195 20 L0 20Z" fill="#fff"/><path d="M0 6 Q97 26 195 0" fill="none" stroke="#0094D4" stroke-width="1.2"/></svg>
  </section>
  <section class="welcome">
    <div class="kicker">Welcome To</div>
    <h2>Harrow Point Metrics</h2>
    <p>Harrow Point Metrics was formed in 2016 to help utilities and regulatory agencies navigate the technical, economic, and policy challenges of building a smarter and cleaner energy future. Through careful research design and sound analysis methods we give program administrators clear, data-driven insights into how technologies and interventions affect the way homes and businesses use energy.</p>
    <span class="btn">Read More</span>
    <div class="deco" role="img" aria-label="Dotted blue wave graphic"></div>
  </section>
  <section class="services">
    <div class="fade"></div><div class="fade r"></div>
    <h2 class="section-title">Our <b>Services</b></h2>
    <span class="arrow left"><svg viewBox="0 0 10 10"><path d="M6 3 L4 5 L6 7" fill="none" stroke="#888" stroke-width=".8"/></svg></span>
    <div class="svc-row">
      <div class="svc blue"><div class="photo" role="img" aria-label="Wind turbines over solar panels"></div><div class="body"><h3>Predictive Analytics and Forecasting</h3><p>Distributed energy resource integration into planning and operations</p><span class="more">Read More</span></div></div>
      <div class="svc gray"><div class="photo" role="img" aria-label="Rows of solar panels in a field"></div><div class="body"><h3>T&amp;D Planning</h3><p>Location specific, probabilistic forecasting for transmission and distribution planning</p><span class="more">Read More</span></div></div>
      <div class="svc blue"><div class="photo" role="img" aria-label="Wind turbines on green hills"></div><div class="body"><h3>Pilot &amp; Emerging Tech Support</h3><p>Design and implementation of pilots and controlled deployments</p><span class="more">Read More</span></div></div>
      <div class="svc gray"><div class="photo" role="img" aria-label="Turbines at sunset"></div><div class="body"><h3>Program Portfolio &amp; Resource Planning</h3><p>End-use load profile studies, saturation research and baseline studies</p><span class="more">Read More</span></div></div>
    </div>
    <span class="arrow right"><svg viewBox="0 0 10 10"><path d="M4 3 L6 5 L4 7" fill="none" stroke="#888" stroke-width=".8"/></svg></span>
  </section>
  <section class="publications">
    <h2 class="section-title">Publications</h2>
    <div class="pub-img a" role="img" aria-label="City lights seen from above at night"></div>
    <div class="pub-text a"><h3>Conference Presentations</h3><p>We share our methods and findings at industry events, covering load impact evaluation, grid planning studies, forecasting models and lessons learned from pilot programs across the country.</p><span class="btn-outline">Read More</span></div>
    <div class="pub-text b"><h3>Reports</h3><p>Our published reports document program impacts, end-use load research, emerging technology pilots and forecasting work prepared for utilities, regulators and research partners.</p><span class="btn-outline">Read More</span></div>
    <div class="pub-img b" role="img" aria-label="Hand pointing at data charts on a screen"></div>
  </section>
  <section class="team">
    <h2 class="section-title">Our <b>Team</b></h2>
    <div class="team-row">
      <div class="member"><div class="avatar" role="img" aria-label="Portrait of Owen Marlow"></div><h3>Owen Marlow, M.S.</h3><div class="role">Partner</div><p>Owen is an applied statistician whose work is centered on estimating the impacts of demand programs.</p><span class="go"><svg viewBox="0 0 10 10"><path d="M3 5 H7 M5.5 3.5 L7 5 L5.5 6.5" fill="none" stroke="#fff" stroke-width=".8"/></svg></span></div>
      <div class="member"><div class="avatar" role="img" aria-label="Portrait of Theo Varga"></div><h3>Theo Varga, M.P.P.</h3><div class="role">Partner</div><p>Theo specializes in advanced analytics using large volumes of hourly and sub-hourly data.</p><span class="go"><svg viewBox="0 0 10 10"><path d="M3 5 H7 M5.5 3.5 L7 5 L5.5 6.5" fill="none" stroke="#fff" stroke-width=".8"/></svg></span></div>
      <div class="member"><div class="avatar" role="img" aria-label="Portrait of Mira Coltrane"></div><h3>Mira Coltrane</h3><div class="role">Partner</div><p>Mira's work has focused on distributed energy resources, from solar panels to electric vehicles.</p><span class="go"><svg viewBox="0 0 10 10"><path d="M3 5 H7 M5.5 3.5 L7 5 L5.5 6.5" fill="none" stroke="#fff" stroke-width=".8"/></svg></span></div>
      <div class="member"><div class="avatar" role="img" aria-label="Portrait of Lena Hartwell"></div><h3>Lena Hartwell, M.S.</h3><div class="role">Partner</div><p>Lena has extensive expertise with analysis of smart meter data and rate design.</p><span class="go"><svg viewBox="0 0 10 10"><path d="M3 5 H7 M5.5 3.5 L7 5 L5.5 6.5" fill="none" stroke="#fff" stroke-width=".8"/></svg></span></div>
    </div>
  </section>
  <section class="about" role="img" aria-label="Wind turbine on a hillside at sunrise">
    <div class="text"><h2>About Us</h2><p>Harrow Point Metrics was formed in 2016 to help utilities and regulatory agencies navigate the technical, economic, and policy challenges of building a smarter and cleaner energy future. Our research focuses on impact analysis as well as predictive and causal analytics. We deliver data-driven insights into how technologies and interventions affect the way homes and businesses use energy and how those in turn affect grid and system planning.</p><span class="btn">Read More</span></div>
    <svg class="about-curve" viewBox="0 0 195 16" preserveAspectRatio="none"><path d="M0 12 Q110 -2 195 10 L195 16 L0 16Z" fill="#1e1f21"/><path d="M0 12 Q110 -2 195 10" fill="none" stroke="#0094D4" stroke-width="1.2"/></svg>
  </section>
  <footer class="site-footer">
    <div class="brand"><span class="mark"></span>Harrow Point Metrics</div>
    <nav class="footer-nav"><span>Home</span><span>Core Services</span><span>About Us</span><span>Our Work</span><span>Blog</span><span>Contact Us</span></nav>
    <div class="contact addr"><span class="ico"><svg viewBox="0 0 10 10"><path d="M5 2.5 a1.8 1.8 0 0 1 1.8 1.8 C6.8 5.6 5 7.5 5 7.5 S3.2 5.6 3.2 4.3 A1.8 1.8 0 0 1 5 2.5Z" fill="#ccc"/></svg></span><span>48 Larkfield Row<br>Suite 2 Brenton, OR 97000</span></div>
    <div class="contact phone"><span class="ico"><svg viewBox="0 0 10 10"><path d="M3.4 2.8 L4.4 2.8 L4.9 4.2 L4.2 4.7 Q4.8 5.8 5.6 6.2 L6.1 5.5 L7.2 6 L7.2 7 Q4.5 7.2 3.4 2.8Z" fill="#ccc"/></svg></span><span>555.210.4478</span></div>
    <span class="getin">Get In Touch</span>
    <div class="socials"><i></i><i></i><i></i></div>
    <div class="copy">© 2022 Harrow Point Metrics All rights reserved</div>
  </footer>
</article>

<!-- variant 5 -->
<article class="page" style="left:954px">
  <header class="site-header">
    <div class="topbar"><span>555.210.4478</span><span>hello@harrowpointmetrics.test</span><i class="dot"></i><i class="dot"></i><i class="dot"></i></div>
    <div class="brand"><span class="mark"></span>Harrow Point Metrics</div>
    <nav class="nav"><span class="active">Home</span><span>Core Services</span><span>About Us</span><span>Our Work</span><span>Blog</span><span>Contact Us</span></nav>
  </header>
  <section class="hero hero-5">
    <div class="slide" role="img" aria-label="Photo of white clouds under a blue sky"></div>
    <div class="hero-title">Harrow Point Metrics</div>
    <div class="hero-sub">Data driven research and insights<br>to build a smarter and cleaner energy future</div>
    <div class="hero-dots"><i></i><i class="on"></i><i></i></div>
    <svg class="hero-curve" viewBox="0 0 195 20" preserveAspectRatio="none"><path d="M0 6 Q97 26 195 0 L195 20 L0 20Z" fill="#fff"/><path d="M0 6 Q97 26 195 0" fill="none" stroke="#0094D4" stroke-width="1.2"/></svg>
  </section>
  <section class="welcome">
    <div class="kicker">Welcome To</div>
    <h2>Harrow Point Metrics</h2>
    <p>Harrow Point Metrics was formed in 2016 to help utilities and regulatory agencies navigate the technical, economic, and policy challenges of building a smarter and cleaner energy future. Through careful research design and sound analysis methods we give program administrators clear, data-driven insights into how technologies and interventions affect the way homes and businesses use energy.</p>
    <span class="btn">Read More</span>
    <div class="deco" role="img" aria-label="Dotted blue wave graphic"></div>
  </section>
  <section class="services">
    <div class="fade"></div><div class="fade r"></div>
    <h2 class="section-title">Our <b>Services</b></h2>
    <span class="arrow left"><svg viewBox="0 0 10 10"><path d="M6 3 L4 5 L6 7" fill="none" stroke="#888" stroke-width=".8"/></svg></span>
    <div class="svc-row">
      <div class="svc blue"><div class="photo" role="img" aria-label="Wind turbines over solar panels"></div><div class="body"><h3>Predictive Analytics and Forecasting</h3><p>Distributed energy resource integration into planning and operations</p><span class="more">Read More</span></div></div>
      <div class="svc gray"><div class="photo" role="img" aria-label="Rows of solar panels in a field"></div><div class="body"><h3>T&amp;D Planning</h3><p>Location specific, probabilistic forecasting for transmission and distribution planning</p><span class="more">Read More</span></div></div>
      <div class="svc blue"><div class="photo" role="img" aria-label="Wind turbines on green hills"></div><div class="body"><h3>Pilot &amp; Emerging Tech Support</h3><p>Design and implementation of pilots and controlled deployments</p><span class="more">Read More</span></div></div>
      <div class="svc gray"><div class="photo" role="img" aria-label="Turbines at sunset"></div><div class="body"><h3>Program Portfolio &amp; Resource Planning</h3><p>End-use load profile studies, saturation research and baseline studies</p><span class="more">Read More</span></div></div>
    </div>
    <span class="arrow right"><svg viewBox="0 0 10 10"><path d="M4 3 L6 5 L4 7" fill="none" stroke="#888" stroke-width=".8"/></svg></span>
  </section>
  <section class="publications">
    <h2 class="section-title">Publications</h2>
    <div class="pub-img a" role="img" aria-label="City lights seen from above at night"></div>
    <div class="pub-text a"><h3>Conference Presentations</h3><p>We share our methods and findings at industry events, covering load impact evaluation, grid planning studies, forecasting models and lessons learned from pilot programs across the country.</p><span class="btn-outline">Read More</span></div>
    <div class="pub-text b"><h3>Reports</h3><p>Our published reports document program impacts, end-use load research, emerging technology pilots and forecasting work prepared for utilities, regulators and research partners.</p><span class="btn-outline">Read More</span></div>
    <div class="pub-img b" role="img" aria-label="Hand pointing at data charts on a screen"></div>
  </section>
  <section class="team">
    <h2 class="section-title">Our <b>Team</b></h2>
    <div class="team-row">
      <div class="member"><div class="avatar" role="img" aria-label="Portrait of Owen Marlow"></div><h3>Owen Marlow, M.S.</h3><div class="role">Partner</div><p>Owen is an applied statistician whose work is centered on estimating the impacts of demand programs.</p><span class="go"><svg viewBox="0 0 10 10"><path d="M3 5 H7 M5.5 3.5 L7 5 L5.5 6.5" fill="none" stroke="#fff" stroke-width=".8"/></svg></span></div>
      <div class="member"><div class="avatar" role="img" aria-label="Portrait of Theo Varga"></div><h3>Theo Varga, M.P.P.</h3><div class="role">Partner</div><p>Theo specializes in advanced analytics using large volumes of hourly and sub-hourly data.</p><span class="go"><svg viewBox="0 0 10 10"><path d="M3 5 H7 M5.5 3.5 L7 5 L5.5 6.5" fill="none" stroke="#fff" stroke-width=".8"/></svg></span></div>
      <div class="member"><div class="avatar" role="img" aria-label="Portrait of Mira Coltrane"></div><h3>Mira Coltrane</h3><div class="role">Partner</div><p>Mira's work has focused on distributed energy resources, from solar panels to electric vehicles.</p><span class="go"><svg viewBox="0 0 10 10"><path d="M3 5 H7 M5.5 3.5 L7 5 L5.5 6.5" fill="none" stroke="#fff" stroke-width=".8"/></svg></span></div>
      <div class="member"><div class="avatar" role="img" aria-label="Portrait of Lena Hartwell"></div><h3>Lena Hartwell, M.S.</h3><div class="role">Partner</div><p>Lena has extensive expertise with analysis of smart meter data and rate design.</p><span class="go"><svg viewBox="0 0 10 10"><path d="M3 5 H7 M5.5 3.5 L7 5 L5.5 6.5" fill="none" stroke="#fff" stroke-width=".8"/></svg></span></div>
    </div>
  </section>
  <section class="about" role="img" aria-label="Wind turbine on a hillside at sunrise">
    <div class="text"><h2>About Us</h2><p>Harrow Point Metrics was formed in 2016 to help utilities and regulatory agencies navigate the technical, economic, and policy challenges of building a smarter and cleaner energy future. Our research focuses on impact analysis as well as predictive and causal analytics. We deliver data-driven insights into how technologies and interventions affect the way homes and businesses use energy and how those in turn affect grid and system planning.</p><span class="btn">Read More</span></div>
    <svg class="about-curve" viewBox="0 0 195 16" preserveAspectRatio="none"><path d="M0 12 Q110 -2 195 10 L195 16 L0 16Z" fill="#1e1f21"/><path d="M0 12 Q110 -2 195 10" fill="none" stroke="#0094D4" stroke-width="1.2"/></svg>
  </section>
  <footer class="site-footer">
    <div class="brand"><span class="mark"></span>Harrow Point Metrics</div>
    <nav class="footer-nav"><span>Home</span><span>Core Services</span><span>About Us</span><span>Our Work</span><span>Blog</span><span>Contact Us</span></nav>
    <div class="contact addr"><span class="ico"><svg viewBox="0 0 10 10"><path d="M5 2.5 a1.8 1.8 0 0 1 1.8 1.8 C6.8 5.6 5 7.5 5 7.5 S3.2 5.6 3.2 4.3 A1.8 1.8 0 0 1 5 2.5Z" fill="#ccc"/></svg></span><span>48 Larkfield Row<br>Suite 2 Brenton, OR 97000</span></div>
    <div class="contact phone"><span class="ico"><svg viewBox="0 0 10 10"><path d="M3.4 2.8 L4.4 2.8 L4.9 4.2 L4.2 4.7 Q4.8 5.8 5.6 6.2 L6.1 5.5 L7.2 6 L7.2 7 Q4.5 7.2 3.4 2.8Z" fill="#ccc"/></svg></span><span>555.210.4478</span></div>
    <span class="getin">Get In Touch</span>
    <div class="socials"><i></i><i></i><i></i></div>
    <div class="copy">© 2022 Harrow Point Metrics All rights reserved</div>
  </footer>
</article>

</main>
</body>
</html>
```